WP website design (Harrowgate)

We need a wordpress design for an established auction and real estate company based in Florida. The winning design will incorporate a professional color scheme with company logo in a clean layout. The design needs to consider that this will be developed on a responsive theme. Colors are those that will highlight the logo.

Industry/Entity Type

Real Estate

Font styles to use
Serif
Sans Serif

Colors

Designer to choose colors to be used in the design.

Requirements
Must have
• Navigation:
1) Home
2) Auctions
3) Online Auctions
4) About Us
5) Services
6) Real Estate Listings
7) References
8) Contact Us

Colors will be blue (#000066) / red (#B10000) and black or other complementary color. Tagline to be used "Since 1977, Proven Results." Slideshow to be placed in the header or body of home page - please use stock real estate image.

Widgets: 1) Email Sign-up 2) Social media icons for FB and LinkedIn 3) Featured Listings 4) Testimonials 5) Register button

Footer will have smaller company logo, attached logos and contact info:
Phone: (555) 261-0948 Mobile: (555) 718-3062
Email: mirelharrowgate@quellmail.example
Address: 58 E. Tamsin Avenue, Ste 410, Pensacola, FL 32599
Nice to have
• Use of a drop down menu:
Auctions-
1) Upcoming Auctions
2) Past Auctions

```html
<!DOCTYPE html>
<html lang="en">
<head>
<meta charset="utf-8">
<title>Harrowgate Auctions</title>
<link rel="stylesheet" href="https://fonts.googleapis.com/css2?family=Russo+One&family=Exo+2:wght@400;600;700&family=Ubuntu:wght@500;700&family=Arimo:ital,wght@0,400;0,700;1,700&display=swap">
<style>
:root{
  --blue:#2d3190;
  --red:#d81f2b;
  --red-dark:#b3121c;
  --page:#efefef;
  --ink:#222;
  --footer:#363636;
  --white:#fff;
  --black:#1a1a1a;
}
*{box-sizing:border-box;margin:0;padding:0}
html,body{width:928px;height:1200px;overflow:hidden;background:var(--page)}
body{position:relative;font-family:"Arimo",Arial,sans-serif;color:var(--ink)}
.abs{position:absolute}

/* header */
.brand{left:78px;top:12px;display:flex;align-items:center;gap:12px;height:48px}
.brand-mark{width:46px;height:46px;background:var(--blue)}
.brand-name{font-family:"Russo One",sans-serif;font-size:26px;color:var(--blue)}
.follow{left:664px;top:18px;display:flex;align-items:center;gap:10px;font-family:"Exo 2",sans-serif;font-weight:700;font-size:14px;letter-spacing:1px;color:#444}
.social{width:34px;height:34px;border-radius:50%;background:var(--blue);border:3px solid #dcdcdc;box-shadow:0 4px 4px rgba(0,0,0,.25);margin-left:4px}

/* hero band */
.band{left:0;top:73px;width:928px;height:410px;background:var(--red)}
.nav{left:78px;top:85px;width:772px;height:34px;background:var(--blue);border:1px solid #8a8fd6;border-radius:7px;display:flex;align-items:center;justify-content:space-between;padding:0 13px 0 14px;list-style:none}
.nav li{font-family:"Ubuntu",sans-serif;font-weight:700;font-size:12px;color:var(--white)}
.slider{left:78px;top:133px;width:772px;height:338px;border:5px solid var(--red-dark);background:linear-gradient(180deg,#6f8cc0 0%,#9bb0d0 22%,#b58a5c 45%,#7a5a3a 62%,#2d6fd0 75%,#1b2a4a 100%)}
.dots{left:415px;top:421px;width:117px;height:32px;border-radius:16px;background:linear-gradient(#fafafa,#cfcfcf);box-shadow:0 2px 4px rgba(0,0,0,.4);display:flex;align-items:center;justify-content:center;gap:6px}
.dots span{width:11px;height:11px;border-radius:50%;background:#666}
.dots span.on{width:14px;height:14px;background:var(--blue)}

/* welcome */
.welcome{left:0;top:506px;width:928px;display:flex;justify-content:center;align-items:center;gap:10px;font-family:"Russo One",sans-serif;font-weight:400;font-size:23px;color:var(--blue)}
.welcome .mark{width:27px;height:27px;background:var(--blue)}
.welcome em{font-style:normal;color:var(--red)}
.intro{left:92px;top:550px;width:746px;font-size:10.6px;line-height:15.5px;text-align:center}
.intro p+p{margin-top:15px}

/* featured */
.featured{left:90px;top:698px;width:522px;height:384px;background:var(--white);border-radius:10px}
.featured h2{position:absolute;left:10px;top:12px;font-family:"Russo One",sans-serif;font-weight:400;font-size:15px;color:var(--red);letter-spacing:.6px}
.lot{position:absolute;left:10px;width:500px}
.lot h3{font-family:"Exo 2",sans-serif;font-weight:400;font-size:12.5px;color:#333;letter-spacing:.8px}
.thumb{position:absolute;left:0;top:22px;width:130px;height:80px;border:3px solid #f2f2f2;background:linear-gradient(180deg,#8aa0bf 0%,#d9d4c6 45%,#6b5a4a 75%,#1a1f2a 100%)}
.info{position:absolute;left:137px;top:22px;width:360px;font-size:10px;line-height:15px}
.info .kind{font-family:"Ubuntu",sans-serif;font-weight:500;font-size:11.5px;color:var(--blue);letter-spacing:.4px;margin-bottom:1px}
.info b{margin-right:4px}
.buttons{position:absolute;left:346px;top:104px;display:flex;gap:5px}
.btn{height:22px;width:70px;border-radius:5px;display:flex;align-items:center;justify-content:center;gap:5px;font-weight:700;font-size:10px;color:var(--white)}
.btn-red{background:var(--red)}
.btn-dark{background:var(--black);width:65px}
.btn svg{width:13px;height:10px}
.sep{position:absolute;left:-10px;top:151px;width:486px;border-top:1px dotted #aaa}

/* sidebar */
.register{left:629px;top:693px;width:212px;height:48px;background:var(--red);border-radius:9px;display:flex;align-items:center;padding-left:16px;gap:8px;font-family:"Russo One",sans-serif;font-size:20px;color:var(--white);letter-spacing:1.5px}
.register svg{width:34px;height:34px}
.signup{left:629px;top:757px;width:212px;height:165px;background:var(--blue);border-radius:9px}
.signup h4{position:absolute;left:0;width:212px;top:14px;text-align:center;font-family:"Exo 2",sans-serif;font-weight:600;font-size:17px;color:var(--white);letter-spacing:.4px}
.field{position:absolute;left:13px;width:190px;height:24px;background:var(--white);border-radius:5px;font-size:10px;color:#888;padding:6px 8px}
.submit{position:absolute;left:128px;top:120px;width:73px;height:29px;border-radius:12px;background:var(--black);border:1px solid #ccc;color:var(--white);font-size:12.5px;display:flex;align-items:center;justify-content:center}
.testimonial{left:629px;top:938px;width:212px;height:144px;background:var(--red);border-radius:9px;color:var(--white)}
.testimonial h4{position:absolute;left:10px;top:6px;font-family:"Exo 2",sans-serif;font-weight:600;font-size:17px}
.testimonial blockquote{position:absolute;left:10px;top:33px;width:192px;font-weight:700;font-size:9px;line-height:13.8px;text-align:justify}
.testimonial .by{position:absolute;right:10px;top:117px;text-align:right;font-weight:700;font-style:italic;font-size:8.5px;line-height:13px}

/* footer */
.footer{left:0;top:1106px;width:928px;height:70px;background:var(--footer)}
.foot-brand{position:absolute;left:90px;top:21px;display:flex;align-items:center;gap:8px}
.foot-brand .mark{width:30px;height:30px;background:var(--white)}
.foot-brand span{font-family:"Russo One",sans-serif;font-size:16px;color:var(--white)}
.badge{position:absolute;top:20px;height:32px;background:#8b8b8b;border-radius:3px}
.contact{left:0;top:1176px;width:928px;height:24px;background:var(--red);color:var(--white);font-size:10px;display:flex;align-items:center;justify-content:center;gap:9px}
</style>
</head>
<body>

<header>
  <div class="abs brand"><span class="brand-mark"></span><span class="brand-name">Harrowgate Auctions</span></div>
  <div class="abs follow">Follow us on
    <span class="social" role="img" aria-label="Professional network profile"></span>
    <span class="social" role="img" aria-label="Social network page"></span>
  </div>
</header>

<div class="abs band"></div>
<ul class="abs nav">
  <li>Home</li><li>Auctions</li><li>Online Auctions</li><li>About Us</li><li>Services</li><li>Real Estate Listings</li><li>References</li><li>Contact Us</li>
</ul>
<div class="abs slider" role="img" aria-label="Slideshow photo of a modern lit house with pool at dusk"></div>
<div class="abs dots"><span></span><span class="on"></span><span></span><span></span><span></span></div>

<h1 class="abs welcome"><span class="mark"></span>Welcome to <em>Harrowgate</em></h1>
<div class="abs intro">
  <p><b>Harrowgate Auction</b> is simply dummy text of the printing and typesetting industry. Lorem Ipsum has been the industry's standard dummy text ever since the 1500s, when an unknown printer took a galley of type and scrambled it to make a type specimen book. It has survived not only five centuries, but also the leap into electronic typesetting, remaining essentially unchanged. It has survived not only five centuries, but also the leap into electronic type-setting, remaining essentially unchanged.</p>
  <p>It was popularised in the 1960s with the release of Pressmark sheets containing Lorem Ipsum passages, and more recently Pressmark sheets containing Lorem Ipsum passages, and more recently containing Lorem Ipsum passages, and more recently</p>
</div>

<section class="abs featured">
  <h2>FEATURED AUCTIONS</h2>
  <div class="lot" style="top:46px">
    <h3>SHOP EQUIPMENT/TOOLS * PORK PROCESSING ITEMS</h3>
    <div class="thumb" role="img" aria-label="Photo of a modern house at dusk"></div>
    <div class="info">
      <div class="kind">LIVE ON-SITE AUCTION</div>
      <div><b>Begins:</b> Saturday, March 16, 2013 at 10:00 AM EDT</div>
      <div><b>Location:</b> 2286 Wrenfield Road Calloway, KY 40099</div>
      <div style="margin-top:2px">Kestrano BS3F High Lift, 600 Series Dalbrook tractor w/Haverton Loader, Dune buggy, 1207 KR Cutditioner: SHOP.</div>
    </div>
    <div class="buttons">
      <span class="btn btn-red"><svg viewBox="0 0 13 10"><rect x="0" y="1" width="5" height="8" rx="1" fill="#fff"/><rect x="7" y="1" width="6" height="1.6" fill="#fff"/><rect x="7" y="4.2" width="6" height="1.6" fill="#fff"/><rect x="7" y="7.4" width="6" height="1.6" fill="#fff"/></svg>Details</span>
      <span class="btn btn-dark"><svg viewBox="0 0 13 10"><rect x="1" y="0.5" width="8" height="9" fill="none" stroke="#fff" stroke-width="1.2"/><path d="M3 3h4M3 5h4M3 7h2" stroke="#fff"/></svg>Details</span>
    </div>
    <div class="sep"></div>
  </div>
  <div class="lot" style="top:224px">
    <h3>SHOP EQUIPMENT/TOOLS * PORK PROCESSING ITEMS</h3>
    <div class="thumb" role="img" aria-label="Photo of a modern house at dusk"></div>
    <div class="info">
      <div class="kind">LIVE ON-SITE AUCTION</div>
      <div><b>Begins:</b> Saturday, March 16, 2013 at 10:00 AM EDT</div>
      <div><b>Location:</b> 2286 Wrenfield Road Calloway, KY 40099</div>
      <div style="margin-top:2px">Kestrano BS3F High Lift, 600 Series Dalbrook tractor w/Haverton Loader, Dune buggy, 1207 KR Cutditioner: SHOP.</div>
    </div>
    <div class="buttons">
      <span class="btn btn-red"><svg viewBox="0 0 13 10"><rect x="0" y="1" width="5" height="8" rx="1" fill="#fff"/><rect x="7" y="1" width="6" height="1.6" fill="#fff"/><rect x="7" y="4.2" width="6" height="1.6" fill="#fff"/><rect x="7" y="7.4" width="6" height="1.6" fill="#fff"/></svg>Details</span>
      <span class="btn btn-dark"><svg viewBox="0 0 13 10"><rect x="1" y="0.5" width="8" height="9" fill="none" stroke="#fff" stroke-width="1.2"/><path d="M3 3h4M3 5h4M3 7h2" stroke="#fff"/></svg>Details</span>
    </div>
  </div>
</section>

<aside>
  <div class="abs register">
    <svg viewBox="0 0 34 34"><rect x="3" y="6" width="22" height="24" rx="2" fill="none" stroke="#fff" stroke-width="3"/><path d="M9 18l4 4 8-10" fill="none" stroke="#fff" stroke-width="3"/><path d="M22 14l9-10" stroke="#fff" stroke-width="4"/></svg>
    REGISTER
  </div>
  <div class="abs signup">
    <h4>Email Sign Up Form</h4>
    <div class="field" style="top:51px">First Name</div>
    <div class="field" style="top:84px">Email Adress</div>
    <div class="submit">Submit</div>
  </div>
  <div class="abs testimonial">
    <h4>Testimonials</h4>
    <blockquote>"Ipsum is simply dummy text of the printing and typesetting industry. Lorem Ipsum has been the industry's standard dummy text ever since the 1500s, when an unknown printer took a galley of type and scrambled it to make a type specimen"</blockquote>
    <div class="by">By Tobin Arledge<br>Posted on Nov 25,2012</div>
  </div>
</aside>

<footer class="abs footer">
  <div class="foot-brand"><span class="mark"></span><span>Harrowgate</span></div>
  <span class="badge" style="left:258px;width:50px" role="img" aria-label="Auctioneers association badge"></span>
  <span class="badge" style="left:322px;width:28px" role="img" aria-label="National auctioneers badge"></span>
  <span class="badge" style="left:361px;width:122px" role="img" aria-label="Realtors association badge"></span>
  <span class="badge" style="left:488px;width:64px" role="img" aria-label="State realtors badge"></span>
  <span class="badge" style="left:576px;width:144px" role="img" aria-label="Local realtors association badge"></span>
  <span class="badge" style="left:738px;width:104px" role="img" aria-label="Distressed property certification badge"></span>
</footer>
<div class="abs contact">
  <span>Phone: (555) 261-0948</span><span>|</span>
  <span>Mobile: (555) 718-3062</span><span>|</span>
  <span>Email: mirelharrowgate@quellmail.example</span><span>|</span>
  <span>Address: 58 E. Tamsin Avenue, Ste 410, Pensacola, FL 32599</span>
</div>

</body>
</html>
```